Home Staging Company needs business card design

We're a home staging company called Brightly Settled Home Staging. We would like a business card design that includes aqua and gray. Our current logo of house within chair is fine but I find we almost always use the logo in one color. I'll upload images of front and back of our current card and our logo. Note that we have dropped "Solutions" from our company name and don't want to include it on the card.

Target Market(s)

Realtors and homeowners - people interested in selling their homes

Contact Information for Business Card

Marisol Thistlewood
Brightly Settled Home Staging
757-555-0193
www.brightlysettled.com
marisol@brightlysettled.com

Font styles to use
Serif
Script

Requirements
Must have
• My logo and contact details
• UPDATE***
• I forgot to say that the company name should be included on the front of the card somehow.

```html
<!DOCTYPE html>
<html lang="en">
<head>
<meta charset="utf-8">
<title>Brightly Settled Home Staging – Business Card</title>
<link rel="stylesheet" href="https://fonts.googleapis.com/css2?family=Playfair+Display:wght@400&family=Roboto+Condensed:wght@400&family=Questrial&display=swap">
<style>
  :root {
    --page: #c9c9c9;
    --card-dark: #3a3d40;
    --card-light: #f2f2f2;
    --aqua: #4aa9b4;
    --ink: #333639;
    --ink-soft: #55585b;
    --white: #f4f4f4;
  }
  * { margin: 0; padding: 0; box-sizing: border-box; }
  html, body { width: 1200px; height: 576px; overflow: hidden; background: var(--page); }
  .canvas { position: relative; width: 1200px; height: 576px; }

  .card {
    position: absolute;
    top: 138px;
    width: 484px;
    height: 293px;
    border-radius: 14px;
    overflow: hidden;
  }

  /* Front */
  .card-front { left: 82px; background: var(--card-dark); }
  .front-name {
    position: absolute;
    left: 0; right: 0; top: 122px;
    text-align: center;
    font-family: "Playfair Display", serif;
    font-weight: 400;
    font-size: 29px;
    color: var(--white);
  }
  .front-url {
    position: absolute;
    left: 0; right: 0; bottom: 14px;
    text-align: center;
    font-family: "Questrial", sans-serif;
    font-size: 13px;
    color: var(--aqua);
  }

  /* Back */
  .card-back { left: 602px; background: var(--card-light); }
  .card-back::after {
    content: "";
    position: absolute;
    left: 0; right: 0; bottom: 0;
    height: 5px;
    background: var(--aqua);
  }
  .brand-block {
    position: absolute;
    left: 26px; top: 90px;
    width: 200px;
    text-align: center;
  }
  .brand-dot {
    display: block;
    width: 48px; height: 48px;
    margin: 0 auto 12px;
    border-radius: 50%;
    background: var(--aqua);
  }
  .brand-name {
    font-family: "Playfair Display", serif;
    font-weight: 400;
    font-size: 17px;
    line-height: 1.25;
    color: var(--ink);
  }

  .contact-block {
    position: absolute;
    left: 256px; top: 92px;
  }
  .person-name {
    font-family: "Roboto Condensed", sans-serif;
    font-size: 20px;
    color: var(--ink);
  }
  .person-name .surname { color: var(--aqua); }
  .person-title {
    margin-top: 4px;
    font-family: "Questrial", sans-serif;
    font-size: 11px;
    color: var(--ink-soft);
  }
  .contact-list { list-style: none; margin-top: 16px; }
  .contact-list li {
    display: flex;
    align-items: center;
    height: 17px;
    margin-bottom: 1px;
    font-family: "Questrial", sans-serif;
    font-size: 12.5px;
    color: var(--ink);
  }
  .contact-list svg { width: 10px; height: 10px; margin-right: 11px; fill: var(--aqua); }
</style>
</head>
<body>
<main class="canvas">
  <section class="card card-front">
    <p class="front-name">Brightly Settled Home Staging</p>
    <p class="front-url">www.brightlysettled.com</p>
  </section>

  <section class="card card-back">
    <div class="brand-block">
      <span class="brand-dot"></span>
      <p class="brand-name">Brightly Settled<br>Home Staging</p>
    </div>

    <div class="contact-block">
      <p class="person-name">Marisol <span class="surname">Thistlewood</span></p>
      <p class="person-title">Managing Director</p>
      <ul class="contact-list">
        <li>
          <svg viewBox="0 0 10 10" aria-hidden="true"><path d="M1 3 Q5 0 9 3 L8 4.5 L6.5 3.8 L6.5 3 Q5 2.6 3.5 3 L3.5 3.8 L2 4.5 Z M2.5 5 H7.5 L8.5 9 H1.5 Z"/></svg>
          757-555-0193
        </li>
        <li>
          <svg viewBox="0 0 10 10" aria-hidden="true"><circle cx="5" cy="5" r="4.3" fill="none" stroke="#4aa9b4" stroke-width="1.1"/><ellipse cx="5" cy="5" rx="1.8" ry="4.3" fill="none" stroke="#4aa9b4" stroke-width="0.9"/><path d="M0.8 5 H9.2" stroke="#4aa9b4" stroke-width="0.9"/></svg>
          www.brightlysettled.com
        </li>
        <li>
          <svg viewBox="0 0 10 10" aria-hidden="true"><path d="M0.5 2 H9.5 V8 H0.5 Z" /><path d="M0.8 2.3 L5 5.6 L9.2 2.3" fill="none" stroke="#f2f2f2" stroke-width="0.9"/></svg>
          marisol@brightlysettled.com
        </li>
      </ul>
    </div>
  </section>
</main>
</body>
</html>
```